Laser Tattoo Removal Business Cards

We are looking for a professional business card design for a laser tattoo removal business. Ideally looking for a black business card design. The name of the business is Brightline Tattoo Removal. We place our cards at local tattoo shops so we ideally are looking for something trendy/edgy to draw both male and female clientele in.

Target Market(s)

Male/Female ages 18-60

Contact Information for Business Card

black background ideally.. hoping to stay within greys, whites and black

Font styles to use
Serif
Sans Serif

Colors
121212
a9a9a9
5c5c5c
f5f5f5
ffffff
7f7f7f
606060
848484
9d9d9d

Requirements
Must have
• Employee Info:
• Melissa Thornbury
• Chief Executive Offer
• m: 919.537.2846
• w: 919.362.4178
• f: 919.685.3907
• mthornbury@brightlinetattooremoval.example
• Address:
• 4615 Oakmere Pkwy, Suite 210
• Raleigh, NC 27654
• Website:
• www.brightlinetattooremoval.example
Nice to have
• Myabe business name on back or logo on back and employee info on the front

```html
<!DOCTYPE html>
<html lang="en">
<head>
<meta charset="utf-8">
<title>Brightline Tattoo Removal – Business Cards</title>
<link rel="stylesheet" href="https://fonts.googleapis.com/css2?family=Roboto:wght@400&family=Roboto+Condensed:wght@400;500&display=swap">
<style>
  :root {
    --ink: #121212;
    --ink-soft: #2a2a2a;
    --text-grey: #5c5c5c;
    --mid-grey: #7f7f7f;
    --stripe-grey: #9d9d9d;
    --rule-grey: #848484;
    --paper: #f5f5f5;
    --white: #ffffff;
    --backdrop: #dcdcdc;
  }
  * { margin: 0; padding: 0; box-sizing: border-box; }
  html, body { width: 1200px; height: 960px; overflow: hidden; }
  body { background: var(--backdrop); font-family: "Roboto", Arial, sans-serif; }

  .stage { position: relative; width: 1200px; height: 960px; }

  .card { position: absolute; overflow: hidden; }

  /* Front */
  .card--front { left: 315px; top: 113px; width: 572px; height: 342px; background: var(--paper); }

  .brand { position: absolute; right: 28px; top: 52px; width: 240px; text-align: center;
           font-family: "Roboto Condensed", Arial, sans-serif; font-weight: 400; color: var(--ink-soft);
           letter-spacing: 2px; }
  .brand__name { font-size: 38px; line-height: 1; }
  .brand__tag { font-size: 17px; line-height: 1; margin-top: 38px; letter-spacing: 3px; }
  .card--back .brand { color: var(--white); }

  .nameplate { position: absolute; left: 13px; top: 157px; width: 300px; height: 72px; }
  .nameplate svg { position: absolute; inset: 0; }
  .nameplate__name { position: absolute; left: 17px; top: 20px; color: var(--white);
                     font-family: "Roboto Condensed", Arial, sans-serif; font-weight: 500; font-size: 21px; letter-spacing: 0.2px; }
  .nameplate__title { position: absolute; left: 17px; top: 44px; color: var(--white);
                      font-size: 14px; }
  .divider { position: absolute; left: 300px; top: 228px; width: 266px; height: 2px; background: var(--rule-grey); }

  .contacts { position: absolute; left: 31px; top: 243px; list-style: none; font-size: 13px; color: var(--text-grey); }
  .contacts li { display: flex; align-items: center; height: 19px; white-space: nowrap; }
  .contacts svg { width: 12px; height: 12px; margin-right: 10px; fill: var(--ink-soft); flex: none; }

  .address { position: absolute; right: 5px; top: 249px; text-align: right; font-size: 13px;
             line-height: 19px; color: var(--text-grey); font-style: normal; white-space: nowrap; }

  /* Back */
  .card--back { left: 311px; top: 472px; width: 600px; height: 343px; background: var(--ink); }
  .card--back .brand { right: 40px; top: 206px; }
</style>
</head>
<body>
<main class="stage">

  <section class="card card--front" aria-label="Business card front">
    <div class="brand">
      <div class="brand__name">BRIGHTLINE</div>
      <div class="brand__tag">TATTOO REMOVAL</div>
    </div>

    <div class="nameplate">
      <svg width="300" height="72" viewBox="0 0 300 72" aria-hidden="true">
        <polygon points="236,0 248,0 292,72 280,72" fill="var(--stripe-grey)"/>
        <polygon points="0,0 232,0 276,72 0,72" fill="var(--ink-soft)"/>
      </svg>
      <div class="nameplate__name">MELISSA THORNBURY</div>
      <div class="nameplate__title">Chief Executive Offer</div>
    </div>
    <div class="divider"></div>

    <ul class="contacts">
      <li><svg viewBox="0 0 24 24"><path d="M6.6 10.8a15 15 0 0 0 6.6 6.6l2.2-2.2c.3-.3.7-.4 1-.2 1.1.4 2.3.6 3.6.6.6 0 1 .4 1 1V20c0 .6-.4 1-1 1A17 17 0 0 1 3 4c0-.6.4-1 1-1h3.5c.6 0 1 .4 1 1 0 1.3.2 2.5.6 3.6.1.3 0 .7-.2 1z"/></svg>919.362.4178</li>
      <li><svg viewBox="0 0 24 24"><path d="M7 1h10a2 2 0 0 1 2 2v18a2 2 0 0 1-2 2H7a2 2 0 0 1-2-2V3a2 2 0 0 1 2-2zm0 3v14h10V4zm5 15.5a1 1 0 1 0 0 2 1 1 0 0 0 0-2z"/></svg>919.537.2846</li>
      <li><svg viewBox="0 0 24 24"><path d="M6 2h12v5H6zM3 8h18a2 2 0 0 1 2 2v7h-4v5H5v-5H1v-7a2 2 0 0 1 2-2zm4 8v4h10v-4z"/></svg>919.685.3907</li>
      <li><svg viewBox="0 0 24 24"><path d="M2 5h20v14H2zm2 2v.5l8 5 8-5V7z"/></svg>mthornbury@brightlinetattooremoval.example</li>
    </ul>

    <address class="address">
      4615 Oakmere Pkwy<br>
      Suite 210<br>
      Raleigh, NC 27654<br>
      www.brightlinetattooremoval.example
    </address>
  </section>

  <section class="card card--back" aria-label="Business card back">
    <div class="brand">
      <div class="brand__name">BRIGHTLINE</div>
      <div class="brand__tag">TATTOO REMOVAL</div>
    </div>
  </section>

</main>
</body>
</html>
```